Business Card for beauty technology startup

Design Glimora Business Card for a Beauty, based on the website identity and colors (https://www.glimora-example.com).
Glimora is a beauty tech startup that gathers helpful product info for beauty lovers and consumers (such as availability on stores, price range and product reviews) for makeup products. The card design must be young, colorful but clean, and very modern.

Target Market(s)

woman, 15-35

Industry/Entity Type

Cosmetics

Contact Information for Business Card

Full Name, address, phone

Font styles to use
Other font styles liked:
• Advent Pro

Colors
e34297
86cfc6
ffffff
5c5c5c
e8e8e8
e667a6
b2b2b2

Requirements
Must have
• One full colored side with a creative design and another with card info
• Use Color palette: #95C5C5 and/or #D38AA5
• Use fonts: Advent Pro
• Use website identity: https://www.glimora-example.com
Nice to have
• If needed extra font: Roboto

```html
<!DOCTYPE html>
<html lang="en">
<head>
<meta charset="UTF-8">
<title>Glimora Business Card</title>
<link rel="stylesheet" href="https://fonts.googleapis.com/css2?family=Advent+Pro:wght@300;400;500&family=Open+Sans:wght@400;600&display=swap">
<style>
  :root {
    --bg: #2b2b2b;
    --card: #232323;
    --pink: #e34297;
    --pink-soft: #e667a6;
    --white: #ffffff;
    --grey: #b2b2b2;
  }
  * { margin: 0; padding: 0; box-sizing: border-box; }
  html, body { width: 1200px; height: 716px; overflow: hidden; background: var(--bg); }
  .stage { position: relative; width: 1200px; height: 716px; }
  .card {
    position: absolute; top: 206px; width: 530px; height: 303px;
    background: var(--card); border-radius: 18px;
    box-shadow: 0 10px 30px rgba(0,0,0,.45);
    overflow: hidden;
  }
  .card--front { left: 45px; }
  .card--back { left: 625px; }

  .brand { position: absolute; display: flex; align-items: center; gap: 16px; }
  .brand__dot {
    width: 54px; height: 54px; border-radius: 50%;
    border: 2px solid var(--pink-soft);
  }
  .brand__name {
    font-family: "Advent Pro", sans-serif; font-weight: 400;
    color: var(--pink-soft); letter-spacing: 6px; text-transform: uppercase;
  }
  .card--front .brand { left: 60px; top: 100px; }
  .card--front .brand__name { font-size: 44px; }
  .card--front .site { left: 66px; top: 196px; }

  .site {
    position: absolute;
    font-family: "Open Sans", sans-serif; font-size: 14px;
    color: var(--pink-soft);
  }

  .identity { position: absolute; left: 30px; top: 28px; padding-left: 16px; }
  .identity__bar { position: absolute; left: 0; top: 2px; width: 9px; height: 40px; background: var(--pink); }
  .identity__name { font-family: "Open Sans", sans-serif; font-size: 21px; color: var(--white); line-height: 1.1; }
  .identity__title { font-family: "Open Sans", sans-serif; font-size: 13px; color: var(--pink); }

  .card--back .brand { right: 34px; top: 122px; gap: 12px; }
  .card--back .brand__dot { width: 40px; height: 40px; }
  .card--back .brand__name { font-size: 32px; letter-spacing: 4px; }

  .socials { position: absolute; right: 52px; top: 186px; display: flex; gap: 24px; }
  .socials span { width: 13px; height: 13px; border-radius: 3px; background: var(--pink-soft); opacity: .85; }

  .contact {
    position: absolute; left: 36px; top: 196px;
    font-family: "Open Sans", sans-serif; font-size: 13px; color: var(--white);
    line-height: 1.45;
  }
  .contact__row { display: flex; gap: 8px; align-items: flex-start; }
  .contact__row svg { flex: none; margin-top: 3px; }
  .card--back .site { right: 34px; bottom: 22px; }
</style>
</head>
<body>
<main class="stage">
  <section class="card card--front">
    <div class="brand">
      <span class="brand__dot"></span>
      <span class="brand__name">Glimora</span>
    </div>
    <p class="site">www.glimora-example.com</p>
  </section>

  <section class="card card--back">
    <div class="identity">
      <span class="identity__bar"></span>
      <p class="identity__name">Your Name</p>
      <p class="identity__title">Job Title</p>
    </div>

    <div class="brand">
      <span class="brand__dot"></span>
      <span class="brand__name">Glimora</span>
    </div>
    <div class="socials" aria-hidden="true"><span></span><span></span><span></span><span></span></div>

    <div class="contact">
      <div class="contact__row">
        <svg width="12" height="12" viewBox="0 0 24 24"><path fill="#e34297" d="M6.6 10.8a15 15 0 0 0 6.6 6.6l2.2-2.2a1 1 0 0 1 1-.25 11.4 11.4 0 0 0 3.6.57 1 1 0 0 1 1 1V20a1 1 0 0 1-1 1A17 17 0 0 1 3 4a1 1 0 0 1 1-1h3.5a1 1 0 0 1 1 1c0 1.25.2 2.45.57 3.6a1 1 0 0 1-.25 1z"/></svg>
        <span>000 000 0000</span>
      </div>
      <div class="contact__row">
        <svg width="12" height="12" viewBox="0 0 24 24"><path fill="#e34297" d="M12 2a7 7 0 0 0-7 7c0 5.25 7 13 7 13s7-7.75 7-13a7 7 0 0 0-7-7zm0 9.5A2.5 2.5 0 1 1 12 6.5a2.5 2.5 0 0 1 0 5z"/></svg>
        <span>1480 Marlow Ave, suite 210<br>Brookhaven, Texas 78990</span>
      </div>
    </div>

    <p class="site">www.glimora-example.com</p>
  </section>
</main>
</body>
</html>
```